Letterhead and matching envelope design for a dental office

We need a new stationary design, letterhead and envelope #10, for a dental office in Denver area. We are called Bright Harbor Dental. We want a simple and minimalistic design but not a boring design. I wish to have one good point that makes it look professional. I have attached our logo. Feel free to use either one. I want the design for letterhead and envelope look like a "matching pair" but not look the same. The envelope doesn't have to be white and it will have an address window on bottom left.

Target Market(s)

everyone who visits dentist (adults)

Industry/Entity Type

Dental

Font styles to use
Other font styles liked:
• close to font on logo or something that matches well

Requirements
Must have
• professional
• simple, minimalistic
• unique point that stands out
Nice to have
• matching but not same design for letterhead and envelope
Should not have
• not look like all the other boring designs
• no flowery, distracting feats

```html
<!DOCTYPE html>
<html lang="en">
<head>
<meta charset="utf-8">
<title>Bright Harbor Dental – Stationery</title>
<link href="https://fonts.googleapis.com/css2?family=Source+Sans+3:wght@400;600;700&display=swap" rel="stylesheet">
<style>
  :root {
    --green: #3ab54a;
    --green-pale: #e6f3e4;
    --green-edge: #bfe3c0;
    --paper: #ffffff;
    --backdrop: #e9e9ea;
    --ink: #3a3a3a;
    --ink-soft: #8a8a8a;
    --font: "Source Sans 3", Arial, sans-serif;
  }
  * { box-sizing: border-box; margin: 0; padding: 0; }
  html, body { width: 1200px; height: 799px; overflow: hidden; }
  body { background: var(--backdrop); font-family: var(--font); color: var(--ink); position: relative; }

  .brand { display: flex; align-items: center; gap: 6px; color: var(--green); font-weight: 700; letter-spacing: .04em; text-transform: uppercase; }
  .brand-dot { width: 8px; height: 8px; border-radius: 50%; background: var(--green); flex: none; }

  .web-tag { position: absolute; right: 28px; bottom: 12px; background: var(--green); color: #fff; font-size: 12px; padding: 5px 12px; }

  .decor { position: absolute; background: linear-gradient(120deg, var(--green-pale), #f3f9f2); border-radius: 6px; }

  /* Letterhead */
  .letterhead { position: absolute; left: 70px; top: 110px; width: 400px; height: 566px; background: var(--paper); box-shadow: 0 3px 10px rgba(0,0,0,.12); border-bottom: 6px solid var(--green-edge); }
  .letterhead .brand { position: absolute; right: 28px; top: 30px; font-size: 12px; }
  .letter-body { position: absolute; left: 36px; right: 36px; top: 90px; font-size: 8.5px; line-height: 1.5; color: var(--ink-soft); }
  .letter-body .salutation { color: var(--ink); font-weight: 700; font-size: 11px; margin-bottom: 8px; }
  .letter-body p { margin-bottom: 7px; }
  .signature { width: 70px; height: 26px; margin-top: 10px; background: linear-gradient(90deg, #d9d9d9, #f0f0f0); border-radius: 3px; }
  .letterhead .decor { left: 30px; right: 30px; top: 300px; height: 200px; }

  /* Envelope back */
  .envelope-back { position: absolute; left: 510px; top: 90px; width: 620px; height: 270px; background: var(--paper); box-shadow: 0 3px 10px rgba(0,0,0,.12); overflow: hidden; }
  .envelope-back svg.flap { position: absolute; inset: 0; }
  .return-address { position: absolute; right: 30px; top: 18px; font-size: 9.5px; line-height: 1.45; color: var(--ink); }
  .return-address .name { color: var(--green); font-weight: 700; }
  .contact-line { display: flex; align-items: center; gap: 4px; }
  .contact-line svg { flex: none; }
  .envelope-back .brand { position: absolute; right: 70px; top: 170px; color: #fff; font-size: 12px; }
  .envelope-back .brand-dot { background: #fff; }

  /* Envelope front */
  .envelope-front { position: absolute; left: 510px; top: 400px; width: 620px; height: 270px; background: var(--paper); box-shadow: 0 3px 10px rgba(0,0,0,.12); border-bottom: 6px solid var(--green-edge); }
  .envelope-front .brand { position: absolute; left: 30px; top: 26px; font-size: 12px; }
  .envelope-front .decor { left: 270px; top: 60px; width: 250px; height: 150px; }
  .sender { position: absolute; left: 30px; bottom: 40px; font-size: 12px; line-height: 1.3; }
  .sender .name { color: var(--green); font-weight: 700; }
</style>
</head>
<body>

<section class="letterhead">
  <div class="brand"><span class="brand-dot"></span>Bright Harbor Dental</div>
  <div class="letter-body">
    <p class="salutation">Dear Mr. Carter,</p>
    <p>Thank you for choosing our practice for your dental care. We look forward to welcoming you and your family at your next visit this season.</p>
    <p>Our team offers gentle cleanings, checkups and modern treatments in a calm and friendly setting, with flexible hours for busy schedules.</p>
    <p>Please call our office to confirm your appointment or to ask any questions about your care plan. We are always happy to help.</p>
    <div class="signature" role="img" aria-label="Handwritten signature"></div>
  </div>
  <div class="decor" role="img" aria-label="Faint leaf decoration"></div>
  <div class="web-tag">www.brightharbordental.com</div>
</section>

<section class="envelope-back">
  <svg class="flap" width="620" height="270" viewBox="0 0 620 270" aria-hidden="true">
    <path d="M0 0 H620 V230 Q600 250 560 245 Q300 150 0 20 Z" fill="var(--green)"/>
  </svg>
  <div class="return-address" style="background:#fff;padding:4px 6px;">
    <div class="name">Bright Harbor Dental</div>
    <div>2815 Cedar Ridge Ave,</div>
    <div>Suite 210 Lakewood, CO 80226</div>
    <div class="contact-line">
      <svg width="9" height="9" viewBox="0 0 10 10"><circle cx="5" cy="5" r="5" fill="var(--green)"/><path d="M3 2.5 L4.2 2.5 L4.6 4 L4 4.5 Q4.8 6 6 6.4 L6.5 5.8 L8 6.2 L8 7.4 Q5 8 2.6 4 Z" fill="#fff"/></svg>
      303-555-0142
    </div>
    <div class="contact-line">
      <svg width="9" height="9" viewBox="0 0 10 10"><circle cx="5" cy="5" r="5" fill="var(--green)"/><rect x="2.5" y="3.2" width="5" height="3.6" fill="none" stroke="#fff" stroke-width=".8"/><path d="M2.5 3.2 L5 5.2 L7.5 3.2" fill="none" stroke="#fff" stroke-width=".8"/></svg>
      info@brightharbordental.com
    </div>
  </div>
  <div class="brand"><span class="brand-dot"></span>Bright Harbor Dental</div>
</section>

<section class="envelope-front">
  <div class="brand"><span class="brand-dot"></span>Bright Harbor Dental</div>
  <div class="decor" role="img" aria-label="Faint leaf decoration"></div>
  <div class="sender">
    <div class="name">Bright Harbor Dental</div>
    <div>2815 Cedar Ridge Ave, Suite 210 Lakewood, CO 80226</div>
  </div>
  <div class="web-tag">www.brightharbordental.com</div>
</section>

</body>
</html>
```